A website for a Maltese Law Firm

Our law firm needs a website to further its business. The site should have a simple yet effective design. We would need the following sections: About us, Practice Areas, About Malta, Contact. These should be further split as follows:

About us: Our firm, Our values, What others say, Offices

Practice Areas: Crimimal, Citizenship & Residence, Sovereign Patron Pathway, Criminal Defence, Civil Litigation, Arbitration and ADR, Commercial and Corporate, Media Law.

About Malta: just one section.

Contact: Just one section

We would also need a news feed at the front of the site to include latest news regarding our cases.

At the bottom we need a section for our Terms and a Privacy Statement.

Our logo is being attached.

Target Market(s)

All clients looking for legal assistance in Malta

Industry/Entity Type

Legal

Coding

Coded - Design and coding required

Number of Pages Required

1 page

Requirements
Must have
• It must be simple yet striking.

```html
<!DOCTYPE html>
<html lang="en">
<head>
<meta charset="utf-8">
<title>Falzon &amp; Grech Advocates</title>
<link rel="stylesheet" href="https://fonts.googleapis.com/css2?family=Libre+Baskerville:wght@400;700&family=Montserrat:wght@600;700&family=Open+Sans:wght@400;600;700&display=swap">
<style>
:root{
  --ink:#111;
  --black:#000;
  --text:#333;
  --muted:#777;
  --rule:#d8d8d8;
  --panel:#efefef;
  --nav-active:#7a7a7a;
  --accent:#c0673a;
  --dark:#262626;
  --white:#fff;
  --social-blue:#28a9e0;
}
*{box-sizing:border-box;margin:0;padding:0}
html,body{width:700px;height:1200px;overflow:hidden;background:var(--white)}
body{font-family:"Open Sans",Arial,sans-serif;color:var(--text);position:relative}
.abs{position:absolute}

/* header */
.wordmark{font-family:"Libre Baskerville",Georgia,serif;font-weight:400;color:var(--ink);white-space:nowrap}
.header-wordmark{left:77px;top:26px;font-size:13px}
.address{left:512px;top:10px;font-size:7.5px;line-height:11px;color:var(--text)}
.address .label{font-size:7px;letter-spacing:.3px;margin-bottom:3px}

/* navigation */
.nav{left:0;top:55px;width:700px;height:28px;background:var(--black)}
.nav a{position:absolute;top:0;height:28px;line-height:28px;color:var(--white);text-decoration:none;font-family:"Libre Baskerville",Georgia,serif;font-size:8px;text-align:center}
.nav a.active{background:var(--nav-active)}
.search{left:547px;top:6px;width:70px;height:17px;border-bottom:1px solid var(--accent);color:#888;font-size:6.5px;line-height:15px;padding-left:10px}
.search svg{position:absolute;right:4px;top:4px}

/* hero */
.hero{left:0;top:83px;width:700px;height:278px;background:linear-gradient(100deg,#2b1f17 0%,#5a463a 30%,#7a6556 50%,#4a3b33 72%,#1e1815 100%)}
.hero-title{left:354px;top:229px;font-family:"Montserrat",Arial,sans-serif;font-weight:700;font-size:21px;line-height:27px;color:var(--white);letter-spacing:.5px}
.hero-dashes{left:354px;top:301px;display:flex;gap:7px}
.hero-dashes span{width:17px;height:2px;background:var(--white)}

/* practice areas */
.section-title{left:0;top:378px;width:700px;text-align:center;font-family:"Libre Baskerville",Georgia,serif;font-weight:700;font-size:12px;color:var(--ink)}
.area{width:133px;height:119px;text-align:center;padding:0 8px}
.area.highlight{background:var(--panel)}
.area svg{display:block;margin:8px auto 0}
.area h3{font-family:"Libre Baskerville",Georgia,serif;font-size:9px;line-height:11px;color:var(--ink);height:24px;display:flex;align-items:center;justify-content:center;border-bottom:1px solid var(--rule);margin-top:3px;padding-bottom:2px}
.area p{font-size:6.2px;line-height:8.3px;color:var(--muted);margin-top:6px;padding:0 4px}

/* about + news */
.info{left:0;top:671px;width:700px;height:213px;background:linear-gradient(#e8e8e8,#f8f8f8)}
.divider{left:344px;top:680px;width:1px;height:195px;background:var(--rule)}
.heading{font-family:"Libre Baskerville",Georgia,serif;font-weight:400;font-size:17px;color:var(--ink)}
.about-text{left:95px;top:720px;width:237px;font-size:7.2px;line-height:11.2px;color:var(--ink);text-align:justify}
.btn-dark{background:var(--dark);color:var(--white);font-size:7px;letter-spacing:.4px;text-align:center}
.news{left:363px;width:245px}
.date{left:0;top:0;width:32px;height:36px;background:var(--white);text-align:center;font-family:"Libre Baskerville",Georgia,serif;color:var(--ink);line-height:1}
.date b{display:block;font-size:13px;font-weight:400;padding-top:6px}
.date span{display:block;font-size:7px;margin-top:1px}
.news h4{position:absolute;left:42px;top:-2px;width:205px;font-family:"Libre Baskerville",Georgia,serif;font-weight:400;font-size:8.6px;line-height:11px;color:var(--ink)}
.news p{position:absolute;left:42px;top:25px;width:205px;font-size:6.6px;line-height:11px;color:var(--ink)}
.news .btn-dark{position:absolute;left:42px;top:51px;width:44px;height:13px;line-height:13px;font-size:5.5px}

/* contact band */
.touch{left:0;top:884px;width:355px;height:180px;background:linear-gradient(120deg,#eef0ee,#f7f7f5 50%,#e6e8e6)}
.touch-title{left:130px;top:899px;font-family:"Libre Baskerville",Georgia,serif;font-weight:400;font-size:9px;color:var(--ink)}
.field{left:133px;width:140px;height:16px;background:rgba(255,255,255,.75);border:1px solid #e0e0e0;font-size:6.5px;line-height:14px;padding-left:9px;color:#555}
.send{left:148px;top:1028px;width:111px;height:20px;line-height:20px;background:var(--black);color:var(--white);font-family:"Montserrat",Arial,sans-serif;font-size:7.5px;font-weight:600;text-align:center;letter-spacing:.3px}
.contact{left:355px;top:884px;width:345px;height:180px;background:linear-gradient(135deg,#2c2c2c,#1e1e1e);color:var(--white)}
.contact-title{left:27px;top:14px;font-family:"Libre Baskerville",Georgia,serif;font-weight:400;font-size:9px;color:var(--white)}
.contact-wordmark{left:27px;top:37px;font-size:15px;color:var(--white)}
.c-line{font-size:6.3px;line-height:11px;font-weight:600;color:var(--white)}
.social{top:110px;width:17px;height:17px;background:#111}
.social.on{background:var(--social-blue)}
.team{top:136px;font-size:6.3px;font-weight:700;line-height:8px;color:var(--white);white-space:nowrap}
.team small{display:block;font-size:4.8px;font-weight:600}
.team.sep{border-left:1px solid #bbb;padding-left:6px}

/* footer */
.footer{left:0;top:1064px;width:700px;height:136px;background:var(--black);color:var(--white);text-align:center}
.foot-nav{top:16px;width:700px;font-family:"Libre Baskerville",Georgia,serif;font-size:6.4px;color:var(--white);letter-spacing:.2px}
.foot-nav span{margin:0 6px}
.foot-rule{left:77px;width:546px;height:1px;background:#333}
.privacy-title{top:50px;width:700px;font-family:"Libre Baskerville",Georgia,serif;font-size:7px;color:var(--white)}
.privacy-text{left:110px;top:62px;width:480px;font-size:6.1px;line-height:11px;color:var(--white)}
.copy{top:116px;width:700px;font-size:6.2px;color:var(--white)}
</style>
</head>
<body>

<header>
  <div class="wordmark header-wordmark abs">Falzon &amp; Grech Advocates</div>
  <div class="address abs">
    <div class="label">ADDRESS</div>
    12 / 7, Merchant Lane, Valletta<br>
    209, Harbour Road, Birkirkara
  </div>
</header>

<nav class="nav abs">
  <a class="active" style="left:77px;width:84px">Home</a>
  <a style="left:161px;width:75px">About us</a>
  <a style="left:236px;width:106px">Practice Areas</a>
  <a style="left:342px;width:92px">About Malta</a>
  <a style="left:434px;width:97px">Contact us</a>
  <div class="search abs">Search
    <svg width="8" height="8" viewBox="0 0 10 10"><circle cx="4" cy="4" r="3" fill="none" stroke="#fff" stroke-width="1.6"/><line x1="6.3" y1="6.3" x2="9.3" y2="9.3" stroke="#fff" stroke-width="1.8"/></svg>
  </div>
</nav>

<section>
  <div class="hero abs" role="img" aria-label="Photograph of a smiling lawyer in a suit inside a courthouse hall, colleagues talking in the background"></div>
  <h1 class="hero-title abs">WE ARE A LAW FIRM<br>FROM MALTA</h1>
  <div class="hero-dashes abs"><span></span><span></span><span></span><span></span></div>
</section>

<section>
  <h2 class="section-title abs">OUR PRACTICE AREAS ARE</h2>

  <div class="area highlight abs" style="left:77px;top:415px">
    <svg width="24" height="22" viewBox="0 0 24 22"><circle cx="6" cy="15" r="5" fill="none" stroke="#111" stroke-width="2"/><circle cx="17" cy="15" r="5" fill="none" stroke="#111" stroke-width="2"/><path d="M9 9 Q12 2 15 9" fill="none" stroke="#111" stroke-width="2"/></svg>
    <h3>CRIMINAL</h3>
    <p>Skilled counsel for every stage of a criminal matter, from first inquiry to final hearing.</p>
  </div>
  <div class="area abs" style="left:215px;top:415px">
    <svg width="26" height="24" viewBox="0 0 26 24"><path d="M2 12 L13 2 L24 12 L22 12 L22 23 L4 23 L4 12Z" fill="#111"/><circle cx="10" cy="13" r="2.2" fill="#fff"/><circle cx="16" cy="13" r="2.2" fill="#fff"/><rect x="8" y="16" width="4" height="6" fill="#fff"/><rect x="14" y="16" width="4" height="6" fill="#fff"/></svg>
    <h3>CITIZENSHIP &amp;<br>RESIDENCE</h3>
    <p>Guidance on residence permits and citizenship routes for families moving to the islands.</p>
  </div>
  <div class="area abs" style="left:353px;top:415px">
    <svg width="26" height="22" viewBox="0 0 26 22"><ellipse cx="13" cy="13" rx="10" ry="7" fill="#111"/><rect x="7" y="18" width="3" height="4" fill="#111"/><rect x="16" y="18" width="3" height="4" fill="#111"/><circle cx="13" cy="4" r="3.5" fill="#111"/></svg>
    <h3>SOVEREIGN PATRON<br>PATHWAY</h3>
    <p>Clear advice on the patron pathway, its steps, its checks and the papers you will need.</p>
  </div>
  <div class="area abs" style="left:491px;top:415px">
    <svg width="22" height="24" viewBox="0 0 22 24"><rect x="1" y="1" width="20" height="22" fill="none" stroke="#111" stroke-width="2"/><circle cx="11" cy="9" r="3" fill="#111"/><rect x="7" y="13" width="8" height="9" fill="#111"/><line x1="6" y1="1" x2="6" y2="23" stroke="#111" stroke-width="1.3"/><line x1="16" y1="1" x2="16" y2="23" stroke="#111" stroke-width="1.3"/></svg>
    <h3>CRIMINAL DEFENCE</h3>
    <p>Firm defence of your rights before the courts, with care, discretion and close support.</p>
  </div>

  <div class="area abs" style="left:77px;top:544px">
    <svg width="30" height="22" viewBox="0 0 30 22"><rect x="4" y="4" width="12" height="6" transform="rotate(-30 10 7)" fill="#111"/><line x1="12" y1="10" x2="22" y2="17" stroke="#111" stroke-width="2.5"/><rect x="2" y="19" width="14" height="3" fill="#111"/><rect x="18" y="19" width="10" height="3" fill="#111"/></svg>
    <h3>CIVIL LITIGATION</h3>
    <p>Representation in civil disputes, contract claims and property cases before every court.</p>
  </div>
  <div class="area abs" style="left:215px;top:544px">
    <svg width="24" height="22" viewBox="0 0 24 22"><path d="M2 7 L12 1 L22 7Z" fill="#111"/><rect x="4" y="8" width="3" height="10" fill="#111"/><rect x="10.5" y="8" width="3" height="10" fill="#111"/><rect x="17" y="8" width="3" height="10" fill="#111"/><rect x="2" y="19" width="20" height="3" fill="#111"/></svg>
    <h3>ARBITRATION<br>AND ADR</h3>
    <p>Swift and private routes to settle disputes through arbitration and mediation services.</p>
  </div>
  <div class="area abs" style="left:353px;top:544px">
    <svg width="30" height="22" viewBox="0 0 30 22"><circle cx="8" cy="8" r="3.5" fill="#111"/><circle cx="15" cy="6" r="4" fill="#111"/><circle cx="22" cy="8" r="3.5" fill="#111"/><path d="M2 20 Q8 11 14 20Z M9 20 Q15 9 21 20Z M16 20 Q22 11 28 20Z" fill="#111"/></svg>
    <h3>COMMERCIAL<br>AND CORPORATE</h3>
    <p>Company set up, mergers, contracts and daily legal support for firms of every size.</p>
  </div>
  <div class="area abs" style="left:491px;top:544px">
    <svg width="22" height="22" viewBox="0 0 22 22"><rect x="3" y="6" width="12" height="10" rx="1.5" fill="#111"/><path d="M15 11 L20 7 L20 15Z" fill="#111"/></svg>
    <h3>MEDIA LAW</h3>
    <p>Advice on press, broadcast, defamation and online content for media and publishers.</p>
  </div>
</section>

<section>
  <div class="info abs"></div>
  <div class="divider abs"></div>
  <h2 class="heading abs" style="left:95px;top:685px">About Us</h2>
  <div class="about-text abs">
    <p>Natoque eu placerat nunc quisque parturient vestibulum id orci ad dignissim quam cum scelerisque vestibulum aptent fusce maecenas ultricies. Tincidunt quis nec etiam at amet arcu blandit a arcu leo aliquam ornare natoque malesuada eu ante a consectetur a nullam ullamcorper.</p>
    <p style="margin-top:11px">Lorem maecenas netus cubilia id nam a conubia morbi tempus volutpat rhoncus vestibulum suspendisse fusce pulvinar vestibulum class vestibulum eu sem potenti. Dis amet a a ultricies sapien velit nunc vestibulum vel vestibulum eget adipiscing himenaeos vestibulum scelerisque tincidunt parturient.</p>
  </div>
  <div class="btn-dark abs" style="left:95px;top:847px;width:56px;height:16px;line-height:16px">READ MORE</div>

  <h2 class="heading abs" style="left:361px;top:685px">Latest News</h2>
  <article class="news abs" style="top:718px">
    <div class="date abs"><b>01</b><span>Jun</span></div>
    <h4>Elementum a habitasse senectus parturient eget a dictum suspendisse.</h4>
    <p>Natoque eu placerat nunc quisque parturient vestibulum id orci ad dignissim quam</p>
    <div class="btn-dark">READ MORE</div>
  </article>
  <div class="abs" style="left:363px;top:787px;width:245px;height:1px;background:var(--rule)"></div>
  <article class="news abs" style="top:798px">
    <div class="date abs"><b>01</b><span>Jun</span></div>
    <h4>Elementum a habitasse senectus parturient eget a dictum suspendisse.</h4>
    <p>Natoque eu placerat nunc quisque parturient vestibulum id orci ad dignissim quam.</p>
    <div class="btn-dark">READ MORE</div>
  </article>
</section>

<section>
  <div class="touch abs" role="img" aria-label="Soft, faded photograph of a desk with a keyboard, a plant and office supplies"></div>
  <h2 class="touch-title abs">GET IN TOUCH</h2>
  <div class="field abs" style="top:921px">Enter your name</div>
  <div class="field abs" style="top:945px">Phone Number</div>
  <div class="field abs" style="top:969px">Email</div>
  <div class="field abs" style="top:993px;height:29px">Comment</div>
  <div class="send abs">SEND YOUR ENQUIRE
    <svg width="8" height="8" viewBox="0 0 10 10" style="vertical-align:-1px;margin-left:2px"><path d="M0 5 L10 0 L7 10 L5 6Z" fill="#fff"/></svg>
  </div>

  <div class="contact abs" role="group">
    <h2 class="contact-title abs">CONTACT INFO</h2>
    <div class="wordmark contact-wordmark abs">Falzon &amp; Grech Advocates</div>
    <svg class="abs" style="left:25px;top:74px" width="8" height="10" viewBox="0 0 8 10"><path d="M4 10 L1 5 A3.3 3.3 0 1 1 7 5Z" fill="none" stroke="#fff" stroke-width="1.2"/><circle cx="4" cy="3.6" r="1.1" fill="#fff"/></svg>
    <div class="c-line abs" style="left:38px;top:71px">Falzon &amp; Grech Advocates<br>Suite 14, Harbour Road<br>Birkirkara BKR</div>
    <svg class="abs" style="left:146px;top:73px" width="8" height="8" viewBox="0 0 10 10"><path d="M2 0 L4 3 L3 4.5 Q4.5 6.5 5.5 7 L7 6 L10 8 L8.5 10 Q1 8 0 1.5Z" fill="#fff"/></svg>
    <div class="c-line abs" style="left:159px;top:71px">+356 2100 4410</div>
    <svg class="abs" style="left:146px;top:94px" width="8" height="6" viewBox="0 0 8 6"><rect width="8" height="6" fill="#fff"/><path d="M0 0 L4 3.5 L8 0" fill="none" stroke="#222" stroke-width=".8"/></svg>
    <div class="c-line abs" style="left:159px;top:91px">info@falzongrech.mt</div>
    <div class="social abs" style="left:39px"></div>
    <div class="social on abs" style="left:61px"></div>
    <div class="social abs" style="left:83px"></div>
    <div class="team abs" style="left:24px">P. L. Marco Bonello<small>Legal Procurator</small></div>
    <div class="team sep abs" style="left:102px">Av. Dr. Helena Farrugia<small>LL.D. Melit - Associate</small></div>
    <div class="team sep abs" style="left:198px">Av. Dr. Paul Grech<small>LL.D. Melit - Partner</small></div>
  </div>
</section>

<footer class="footer abs">
  <div class="foot-nav abs">HOME<span>-</span>ABOUT US<span>-</span>PRACTICE AREAS<span>-</span>ABOUT MALTA<span>-</span>CONTACT US</div>
  <div class="foot-rule abs" style="top:41px"></div>
  <div class="privacy-title abs">Privacy Policy Statement</div>
  <p class="privacy-text abs">We respect your privacy and only keep the details you share with us for as long as needed to answer your enquiry and handle your case. Your data is never sold or passed to others without consent, and you may ask to see, correct or delete it at any time by writing to our Valletta office.</p>
  <div class="foot-rule abs" style="top:108px"></div>
  <div class="copy abs">© 2016 - www.falzongrech.mt</div>
</footer>

</body>
</html>
```